Brisk Fixwell business card

I need business card for my business, I think you have all my details.six months ago I design with you car wrap design. We would like to design both side of the card. On front of card we would like logo , Name and our contact details.
At the back we are looking to mentioned our services.
The name will be:
Faridoullan Mestor
Managing Director
Ph:07952338417
Email:info@brisk-fixwell.com
Web:www.brisk-fixwell.com
So we have our logo, you don’t need to change the logo.
Please see the attachment.
Thanks

Target Market(s)

Home improvement

Industry/Entity Type

Home Improvement

Contact Information for Business Card

Company name: Brisk Fixwell
Name: Faridoullan Mestor
Position: Director
Ph:07952338417
Web: www.brisk-fixwell.com
Add: 42 Corvale Road
Hounslow
TW3 9KD
SECOND PERSON
Nizamuddel mestor
Position: Handyman
Ph: 07812 564037
Email: info@brisk-fixwell.com
Add: 18 Brackwin Lane Road
Hounslow
TW6 2LB

```html
<!DOCTYPE html>
<html lang="en">
<head>
<meta charset="utf-8">
<title>Brisk Fixwell business card</title>
<link rel="stylesheet" href="https://fonts.googleapis.com/css2?family=Arimo:wght@400;700&display=swap">
<style>
  :root {
    --navy: #23367f;
    --red: #e3171e;
    --ink: #3a3a3a;
    --grey: #8a8a8a;
    --rule: #d6d6d6;
    --paper: #ffffff;
    --backdrop: #2b2b2b;
  }
  * { box-sizing: border-box; margin: 0; padding: 0; }
  html, body { width: 1200px; height: 1015px; overflow: hidden; }
  body {
    background: var(--backdrop);
    font-family: "Arimo", Arial, sans-serif;
    position: relative;
  }
  .card {
    position: absolute;
    width: 620px;
    height: 354px;
    background: var(--paper);
    overflow: hidden;
    box-shadow: 0 14px 30px rgba(0,0,0,.55);
  }
  /* Services side */
  .card--services { left: 80px; top: 90px; padding: 20px 18px; }
  .service-grid {
    display: grid;
    grid-template-columns: repeat(5, 1fr);
    column-gap: 4px;
    row-gap: 14px;
  }
  .service { display: flex; flex-direction: column; }
  .service__photo { height: 118px; }
  .service__label {
    margin-top: 8px;
    text-align: center;
    color: var(--navy);
    font-size: 13px;
    letter-spacing: .5px;
    text-transform: uppercase;
  }
  .tone-plumbing   { background: linear-gradient(135deg, #d9dde2, #9aa1a8); }
  .tone-carpentry  { background: linear-gradient(135deg, #7a5a3e, #c9a273); }
  .tone-painting   { background: linear-gradient(90deg, #f1f1f1 45%, #8fd3ec); }
  .tone-gardening  { background: linear-gradient(180deg, #6e5a44 30%, #4f9a2f); }
  .tone-decking    { background: linear-gradient(135deg, #e8d2b0, #b89468); }
  .tone-fence      { background: linear-gradient(135deg, #cdb56a, #e9862b); }
  .tone-gutter     { background: linear-gradient(135deg, #3a3a3a, #f0eeea 55%, #9c6a4c); }
  .tone-plastering { background: linear-gradient(135deg, #b5a277, #8d7a55); }
  .tone-tilling    { background: linear-gradient(135deg, #eeeeee, #c9c9c9); }
  .tone-flooring   { background: linear-gradient(135deg, #e6e4e0, #7a4f34); }

  /* Contact side */
  .card--contact { left: 500px; top: 575px; }
  .divider { position: absolute; inset: 0; }
  .brand {
    position: absolute;
    left: 50px; top: 150px;
    display: flex; align-items: center; gap: 12px;
  }
  .brand__mark { width: 22px; height: 22px; background: var(--red); }
  .brand__name {
    font-size: 34px; font-weight: 700; color: var(--navy);
    letter-spacing: .5px;
  }
  .contact {
    position: absolute;
    left: 345px; top: 78px;
    color: var(--ink);
  }
  .contact__name {
    color: var(--navy); font-weight: 700; font-size: 19px;
    text-transform: uppercase; letter-spacing: .3px;
  }
  .contact__role {
    color: var(--grey); font-size: 13px; letter-spacing: 1px;
    text-transform: uppercase; margin-top: 2px; margin-bottom: 14px;
  }
  .contact__line {
    display: flex; align-items: center; gap: 9px;
    font-size: 14px; margin-bottom: 6px;
  }
  .contact__line svg { width: 14px; height: 14px; flex: none; fill: var(--navy); }
  .contact__web b { color: var(--navy); font-weight: 400; }
  .contact__address { margin-top: 12px; padding-left: 23px; font-size: 14px; line-height: 1.35; }
  .band { position: absolute; left: 0; bottom: 0; width: 620px; height: 16px; }
</style>
</head>
<body>

<section class="card card--services" aria-label="Card back: services">
  <div class="service-grid">
    <div class="service"><div class="service__photo tone-plumbing" role="img" aria-label="Photo of hands fitting a sink pipe"></div><span class="service__label">Plumbing</span></div>
    <div class="service"><div class="service__photo tone-carpentry" role="img" aria-label="Photo of hands planing wood"></div><span class="service__label">Carpentry</span></div>
    <div class="service"><div class="service__photo tone-painting" role="img" aria-label="Photo of a paint roller on a wall"></div><span class="service__label">Painting</span></div>
    <div class="service"><div class="service__photo tone-gardening" role="img" aria-label="Photo of turf being laid"></div><span class="service__label">Gardening</span></div>
    <div class="service"><div class="service__photo tone-decking" role="img" aria-label="Photo of timber decking boards"></div><span class="service__label">Decking</span></div>
    <div class="service"><div class="service__photo tone-fence" role="img" aria-label="Photo of a worker drilling a fence panel"></div><span class="service__label">Fence</span></div>
    <div class="service"><div class="service__photo tone-gutter" role="img" aria-label="Photo of a gloved hand cleaning a gutter"></div><span class="service__label">Gutter</span></div>
    <div class="service"><div class="service__photo tone-plastering" role="img" aria-label="Photo of plaster being spread with a trowel"></div><span class="service__label">Plastering</span></div>
    <div class="service"><div class="service__photo tone-tilling" role="img" aria-label="Photo of wall tiles being fixed"></div><span class="service__label">Tilling</span></div>
    <div class="service"><div class="service__photo tone-flooring" role="img" aria-label="Photo of laminate flooring being laid"></div><span class="service__label">Flooring</span></div>
  </div>
</section>

<section class="card card--contact" aria-label="Card front: contact details">
  <svg class="divider" viewBox="0 0 620 354" aria-hidden="true">
    <defs>
      <linearGradient id="fade" x1="0" y1="0" x2="0" y2="1">
        <stop offset="0" stop-color="#d6d6d6" stop-opacity="0"/>
        <stop offset=".5" stop-color="#cfcfcf"/>
        <stop offset="1" stop-color="#d6d6d6" stop-opacity="0"/>
      </linearGradient>
    </defs>
    <line x1="295" y1="40" x2="335" y2="300" stroke="url(#fade)" stroke-width="1.2"/>
  </svg>

  <div class="brand">
    <span class="brand__mark" aria-hidden="true"></span>
    <span class="brand__name">Brisk Fixwell</span>
  </div>

  <div class="contact">
    <p class="contact__name">Faridoullan Mestor</p>
    <p class="contact__role">Director</p>
    <p class="contact__line">
      <svg viewBox="0 0 24 24" aria-hidden="true"><path d="M6.6 10.8a15.1 15.1 0 0 0 6.6 6.6l2.2-2.2a1 1 0 0 1 1-.25 11.4 11.4 0 0 0 3.6.57 1 1 0 0 1 1 1V20a1 1 0 0 1-1 1A17 17 0 0 1 3 4a1 1 0 0 1 1-1h3.5a1 1 0 0 1 1 1c0 1.25.2 2.45.57 3.57a1 1 0 0 1-.25 1z"/></svg>
      07952338417
    </p>
    <p class="contact__line">
      <svg viewBox="0 0 24 24" aria-hidden="true"><path d="M2 5h20v14H2z" fill="none"/><path d="M2 5h20l-10 8zM2 7.5l10 8 10-8V19H2z"/></svg>
      info@brisk-fixwell.com
    </p>
    <p class="contact__line contact__web">
      <svg viewBox="0 0 24 24" aria-hidden="true"><path d="M12 2a10 10 0 1 0 0 20 10 10 0 0 0 0-20zm6.9 6h-3a15 15 0 0 0-1.3-4 8 8 0 0 1 4.3 4zM12 4c.8 1.2 1.5 2.5 1.9 4h-3.8c.4-1.5 1.1-2.8 1.9-4zM4.3 14a8 8 0 0 1 0-4h3.4a16 16 0 0 0 0 4zm.8 2h3a15 15 0 0 0 1.3 4 8 8 0 0 1-4.3-4zm3-8h-3a8 8 0 0 1 4.3-4 15 15 0 0 0-1.3 4zM12 20c-.8-1.2-1.5-2.5-1.9-4h3.8c-.4 1.5-1.1 2.8-1.9 4zm2.3-6H9.7a14 14 0 0 1 0-4h4.6a14 14 0 0 1 0 4zm.3 6a15 15 0 0 0 1.3-4h3a8 8 0 0 1-4.3 4zm1.7-6a16 16 0 0 0 0-4h3.4a8 8 0 0 1 0 4z"/></svg>
      <span>www.<b>brisk-fixwell</b>.com</span>
    </p>
    <p class="contact__address">42 Corvale Road<br>Hounslow, TW3 9KD</p>
  </div>

  <svg class="band" viewBox="0 0 620 16" preserveAspectRatio="none" aria-hidden="true">
    <polygon points="0,0 415,0 405,16 0,16" fill="var(--red)"/>
    <polygon points="421,0 620,0 620,16 411,16" fill="var(--navy)"/>
  </svg>
</section>

</body>
</html>
```